Small boutique home based travel agency needs a flyer design and logo

I need a flyer design for my boutique home-based travel agency that specializes in designing personalized trips to Europe, ocean and river cruises and escorted small group tours to exotic destinations.

We are travel experts, provide the best customer service in the industry and would like this promoted. Open by appointment.
Would like the flyer and logo to use a globe and I like color. Please integrate photo.

Boutique

```html
<!DOCTYPE html>
<html lang="en">
<head>
<meta charset="UTF-8">
<title>Boutique Travel Flyer</title>
<link rel="stylesheet" href="https://fonts.googleapis.com/css2?family=Source+Sans+3:wght@400;500&display=swap">
<style>
  :root {
    --teal: #1fb6ad;
    --teal-light: #7fd5cf;
    --sky: #13b2e3;
    --orange: #f47a3b;
    --ink: #141414;
    --paper: #ffffff;
    --rule: #8a8a8a;
  }
  html, body {
    margin: 0;
    padding: 0;
    overflow: hidden;
    background: var(--paper);
  }
  .flyer {
    position: relative;
    width: 1200px;
    height: 927px;
    background: var(--paper);
    border: 1px solid var(--rule);
    box-sizing: border-box;
    overflow: hidden;
    font-family: "Source Sans 3", "Myriad Pro", Arial, sans-serif;
  }
  .info-panel {
    position: absolute;
    left: 23px;
    top: 23px;
    width: 1154px;
    height: 730px;
    background: var(--teal);
    overflow: hidden;
  }
  .world-map {
    position: absolute;
    inset: 40px 20px 60px 20px;
    background:
      radial-gradient(ellipse 18% 30% at 24% 38%, rgba(255,255,255,0.32), rgba(255,255,255,0) 70%),
      radial-gradient(ellipse 10% 22% at 32% 72%, rgba(255,255,255,0.28), rgba(255,255,255,0) 70%),
      radial-gradient(ellipse 14% 16% at 52% 30%, rgba(255,255,255,0.3), rgba(255,255,255,0) 70%),
      radial-gradient(ellipse 12% 24% at 54% 60%, rgba(255,255,255,0.3), rgba(255,255,255,0) 70%),
      radial-gradient(ellipse 26% 26% at 74% 32%, rgba(255,255,255,0.32), rgba(255,255,255,0) 70%),
      radial-gradient(ellipse 10% 10% at 86% 74%, rgba(255,255,255,0.28), rgba(255,255,255,0) 70%);
  }
  .info-text {
    position: absolute;
    top: 30px;
    margin: 0;
    color: var(--ink);
    font-size: 35px;
    font-weight: 400;
    line-height: 51px;
  }
  .info-text--left { left: 60px; }
  .info-text--right { left: 637px; }
  .fold-line {
    position: absolute;
    left: 599px;
    top: 0;
    height: 927px;
    border-left: 1.5px dashed #555;
  }
  .photo-strip { position: absolute; top: 765px; height: 141px; }
  .bar { position: absolute; top: 765px; height: 141px; }
  .bar--sky { background: var(--sky); }
  .bar--orange { background: var(--orange); }
  .bar--teal { background: var(--teal); }
  .photo--coast { background: linear-gradient(180deg, #8fb8d8 0%, #c9a48a 45%, #b86d4e 65%, #2f6f95 100%); }
  .photo--cathedral { background: linear-gradient(180deg, #6fa2d6 0%, #b8cde0 40%, #e6e0d4 62%, #6f9b4a 85%, #5a8a3c 100%); }
  .photo--statue { background: linear-gradient(160deg, #4c5a3a 0%, #8a8b7a 45%, #c8c2b4 60%, #59623f 100%); }
  .photo--gate { background: linear-gradient(180deg, #eef2f5 0%, #cfc4b0 50%, #8d8472 72%, #4e7b3a 100%); }
  .photo--fort { background: linear-gradient(180deg, #4f8fd6 0%, #8dbbe8 40%, #1f5ca8 60%, #c2b49a 80%, #7c6f5a 100%); }
</style>
</head>
<body>
<main class="flyer">
  <section class="info-panel">
    <div class="world-map" role="img" aria-label="Faint world map behind the text"></div>
    <p class="info-text info-text--left">All your information<br>here, services, tours, des-<br>tinations, etc. also more<br>pictures could be added.<br>This block will be smaller<br>and the collage on top,<br>would be bigger. Colors,<br>fonts, pictures, etc. can<br>be changed at your re-<br>quest. The Florence,<br>Paris and Naples images<br>are royalty free and<br>copyright free.</p>
    <p class="info-text info-text--right">All your information<br>here, services, tours, des-<br>tinations, etc. also more<br>pictures could be added.<br>This block will be smaller<br>and the collage on top,<br>would be bigger. Colors,<br>fonts, pictures, etc. can<br>be changed at your re-<br>quest. The Florence,<br>Paris and Naples images<br>are royalty free and<br>copyright free.</p>
  </section>

  <div class="bar bar--sky" style="left:23px;width:39px"></div>
  <div class="photo-strip photo--coast" style="left:73px;width:142px" role="img" aria-label="Photo of a colourful seaside town on the Mediterranean"></div>
  <div class="bar bar--orange" style="left:226px;width:41px"></div>
  <div class="photo-strip photo--cathedral" style="left:276px;width:189px" role="img" aria-label="Photo of a cathedral and leaning tower on a green lawn"></div>
  <div class="bar bar--teal" style="left:477px;width:41px"></div>
  <div class="photo-strip photo--statue" style="left:527px;width:143px" role="img" aria-label="Photo of a classical stone statue among greenery"></div>
  <div class="bar bar--sky" style="left:682px;width:39px"></div>
  <div class="photo-strip photo--gate" style="left:733px;width:190px" role="img" aria-label="Photo of a monumental city gate with gardens"></div>
  <div class="bar bar--orange" style="left:933px;width:40px"></div>
  <div class="photo-strip photo--fort" style="left:985px;width:142px" role="img" aria-label="Photo of a stone watchtower above a blue sea"></div>
  <div class="bar bar--teal" style="left:1138px;width:39px"></div>

  <div class="fold-line" aria-hidden="true"></div>
</main>
</body>
</html>
```